LB - WESITE NEEDED PAGE: Clean / Modern / Pro & Dynamic

Lantern-Brokers is a new insurance brokerage firm dealing exclusively with companies (BToB) providing the following property: Liabilities Insurance Insurances Automobile Insurance Insurances Construction% 26amp; Engineering Casualty Workmen 's Compensation Health Insurance Marime% 26amp; Transit Credit Insurance Young, Fast, Proactive and Dynamic we call ourselves Lantern-Brokers because we are a "start-up" willing to make a difference in the market, bringing modernity and speed to our industry, still too bureaucratic / procedural / opaque uninitiated. We need something respecting the colors of our orange logtype; blue; white; black; easy to scroll, with simple information on the company; - who we are - our team (with the pictures) - what we do - what we do - contact us, contact us (google map) Luanda (Angola) Small company, just need something flashy / professional / structured / modern.

Target Market(s)

BtoB; Oil and gas companies; French speaking copying established in Angola, all industrials, factories and importers of goods.

Industry/Entity Type

Insurance Broker

Font styles to use
Sans Serif

Colors

Designer to choose colors to be used in the design.

Requirements
Must have
• We need something respecting the colors of our orange logtype; blue; white; black; easy to scroll, with simple information on the company; - who we are - our team (with the pictures) - what we do - what we do - contact us, contact us (google map) Luanda (Angola) Small company, just need something flashy / professional / structured / modern.
Nice to have
• A page format
Should not have
• WE DO NOT WANT A REFER TO OUR LOGO, but a Home Page for our Website with the basics categories ... >> PLEASE CAREFULLY USE THE RIGHT COLOR OF THE LOGOTYPE which are the ones enclosed Orange / Turquoise / Black as per the business card .

```html
<!DOCTYPE html>
<html lang="en">
<head>
<meta charset="utf-8">
<title>Lantern Insurance Brokers</title>
<link rel="stylesheet" href="https://fonts.googleapis.com/css2?family=Exo+2:wght@600;700&family=Montserrat:ital,wght@0,400;0,500;0,600;1,500&display=swap">
<style>
:root{
  --orange:#f2582a;
  --orange-2:#ff7a3d;
  --blue:#0a93ec;
  --ink:#1b1b1b;
  --muted:#9a9a9a;
  --header:#2c3446;
  --light:#f6f6f6;
  --footer:#070707;
  --white:#ffffff;
}
*{box-sizing:border-box;margin:0;padding:0}
html,body{width:1200px;height:3578px;overflow:hidden}
body{position:relative;font-family:'Montserrat',sans-serif;color:var(--ink);background:var(--white)}
.abs{position:absolute}
.heading{font-family:'Exo 2',sans-serif;font-weight:700}
.center{left:0;width:1200px;text-align:center}
.kicker{color:var(--blue);font-size:13px}
.lead{color:var(--muted);font-size:11px}
.btn{display:flex;align-items:center;justify-content:center;background:linear-gradient(90deg,var(--orange),var(--orange-2));color:var(--white);font-size:12px;font-weight:600;border-radius:18px}
.btn-dot{position:absolute;left:-12px;width:28px;height:28px;border-radius:50%;background:var(--blue)}
.underline{height:2px;width:60px;background:var(--blue);left:570px}

/* header */
.site-header{top:0;left:0;width:1200px;height:71px;background:var(--header)}
.brand{top:22px;left:148px;display:flex;align-items:center;gap:8px;color:var(--orange);font-size:14px;font-weight:600}
.brand-mark{width:22px;height:22px;border-radius:50%;background:var(--blue)}
.nav{top:29px;left:323px;display:flex;gap:32px;color:var(--white);font-size:11.5px;font-weight:500}
.nav .active{color:var(--orange)}
.nav-phone{top:22px;left:935px;display:flex;align-items:center;gap:10px;color:var(--white);font-size:12.5px}

/* hero */
.hero-photo{top:71px;left:0;width:1200px;height:549px;background:linear-gradient(100deg,#f1f1f0 0%,#e4e6e8 38%,#9aa5b5 62%,#3b4658 85%,#2a3140 100%)}
.hero-welcome{top:246px;left:141px;font-size:16px;font-weight:500}
.hero-title{top:270px;left:139px;font-size:39px;line-height:43px;letter-spacing:.5px}
.hero-sub{top:362px;left:141px;width:400px;font-size:12.5px;font-weight:500;line-height:17px}
.scroll-cue{top:595px;left:575px;width:50px;height:36px;border-radius:25px 25px 0 0;background:var(--white)}

/* about */
.about-frame{top:810px;left:155px;width:444px;height:293px;background:var(--white);box-shadow:0 0 12px rgba(0,0,0,.15)}
.about-photo{top:817px;left:163px;width:428px;height:279px;background:linear-gradient(135deg,#dfe6ee,#aeb9c6 55%,#6f7e90)}
.about-title{top:810px;left:636px;width:330px;color:var(--orange);font-size:16px;font-weight:500;line-height:23px}
.about-text{top:864px;left:636px;width:420px;color:var(--muted);font-size:10.5px;line-height:19px;text-align:justify}
.about-rule{top:1030px;left:714px;width:1px;height:32px;background:#ddd}

/* services */
.services{top:1174px;left:0;width:1200px;height:454px;background:var(--light)}
.service{width:200px;text-align:center}
.ring{width:140px;height:140px;margin:0 auto}
.service-label{margin-top:26px;font-size:13px;font-weight:500;line-height:17px}
.service.hot .service-label{color:var(--orange)}

/* testimonial */
.testimonial{top:1628px;left:0;width:1200px;height:443px;background:linear-gradient(90deg,#5b6272,#7b8395 30%,#858da0 70%,#5e6576)}
.testimonial *{color:var(--white)}
.avatar{top:1797px;left:564px;width:72px;height:72px;border-radius:50%;background:#c8ccd4;border:3px solid var(--white)}
.quote{top:1882px;left:270px;width:660px;font-size:11px;line-height:18px;text-align:center}
.dots{top:1993px;left:582px;display:flex;gap:6px}
.dots span{width:7px;height:7px;border-radius:50%;background:var(--white)}
.dots .on{background:var(--orange)}

/* team */
.card{top:2244px;width:213px;height:309px;background:var(--white);border:1px solid #ececec;text-align:center}
.card-photo{height:180px;background:linear-gradient(180deg,#dde2e8,#9ea8b6)}
.card-name{margin-top:22px;font-size:12.5px}
.card-role{margin-top:3px;color:var(--orange);font-size:11.5px;font-style:italic;font-weight:500}
.card-text{margin:10px auto 0;width:180px;color:var(--muted);font-size:10px;line-height:16px}
.card-social{top:2290px;left:376px;width:22px;height:70px;background:var(--white);display:flex;flex-direction:column;align-items:center;justify-content:space-around;border-radius:0 8px 8px 0}
.card-social span{width:8px;height:8px;border-radius:50%;background:var(--ink)}

/* contact */
.contact{top:2618px;left:0;width:1200px;height:507px;background:var(--light)}
.field{height:42px;background:var(--white);border:1px solid #dcdcdc;font-size:10px;padding:14px 14px;color:#444}
.contact-photo{top:2660px;left:625px;width:380px;height:465px;background:linear-gradient(180deg,#c9a88f 0%,#d9e3ee 40%,#b9cbe0 100%);border-radius:160px 160px 0 0}

/* newsletter */
.newsletter{top:3125px;left:0;width:1200px;height:70px;background:var(--blue)}
.news-icon{top:3143px;left:151px;width:36px;height:36px;border-radius:50%;border:2px solid var(--white)}
.news-title{top:3145px;left:198px;color:var(--white);font-size:25px}
.news-input{top:3144px;left:483px;width:353px;height:31px;background:var(--white);font-size:10px;padding:10px 10px}

/* footer */
.footer{top:3195px;left:0;width:650px;height:319px;background:var(--footer)}
.map{top:3195px;left:650px;width:550px;height:319px;background:linear-gradient(135deg,#f2f2f2,#e4e4e4)}
.foot-title{color:var(--white);font-size:21px;letter-spacing:.5px}
.foot-list{list-style:none;color:var(--white);font-size:11px}
.foot-list li{margin-bottom:18px;display:flex;align-items:center;gap:8px}
.foot-list li::before{content:"";width:4px;height:4px;border-radius:50%;background:var(--white)}
.foot-list .active{color:var(--orange)}
.foot-list .active::before{background:var(--orange)}
.f-icon{width:24px;height:24px;background:var(--blue);border-radius:3px;display:flex;align-items:center;justify-content:center}
.f-row{left:414px;display:flex;gap:12px;color:var(--white);font-size:11.5px;line-height:16px}
.copyright{top:3546px;color:#333;font-size:11px}
</style>
</head>
<body>

<header class="abs site-header">
  <div class="abs brand"><span class="brand-mark"></span>Lantern-Brokers</div>
  <nav class="abs nav">
    <span class="active">HOME</span><span>WHO WE ARE</span><span>WHAT WE DO</span><span>TESTIMONIAL</span><span>OUR TEAM</span><span>CONTACT US</span>
  </nav>
  <div class="abs nav-phone">
    <svg width="28" height="28" viewBox="0 0 28 28"><circle cx="14" cy="14" r="13" fill="none" stroke="#f2582a" stroke-width="1.5"/><path d="M10 8l3 3-1.5 2a8 8 0 0 0 3.5 3.5l2-1.5 3 3-2 2c-5 0-10-5-10-10z" fill="#f2582a"/></svg>
    (555) 014 2290
  </div>
</header>

<section>
  <div class="abs hero-photo" role="img" aria-label="Photo of two businessmen discussing at an office desk with a laptop"></div>
  <p class="abs hero-welcome">Welcome To</p>
  <h1 class="abs heading hero-title">LANTERN INSURANCE<br>BROKERS</h1>
  <p class="abs hero-sub">We Are A New Insurance Brokerage Firm Dealing Exclusively With Companies.</p>
  <div class="abs btn" style="top:410px;left:150px;width:132px;height:31px"><span class="btn-dot"></span>CONTACT US</div>
  <div class="abs scroll-cue"></div>
  <svg class="abs" style="top:603px;left:592px" width="16" height="24" viewBox="0 0 16 24"><rect x="2" y="2" width="12" height="20" rx="6" fill="none" stroke="#f2582a" stroke-width="1.5"/><line x1="8" y1="6" x2="8" y2="10" stroke="#f2582a" stroke-width="1.5"/></svg>
</section>

<section>
  <p class="abs center kicker" style="top:694px">About Us</p>
  <h2 class="abs center heading" style="top:710px;font-size:33px">Who We Are</h2>
  <p class="abs center lead" style="top:766px">Lorem ipsum dolor sit amet, consectetuer adipiscing elit, sed diam nonummy nibh euismod tincidunt ut laoreet dolore magna</p>
  <div class="abs about-frame"></div>
  <div class="abs about-photo" role="img" aria-label="Photo of a smiling businesswoman in a meeting"></div>
  <h3 class="abs about-title">WELCOME TO LANTERN INSURANCE BROKERS</h3>
  <p class="abs about-text">Lorem Ipsum Dolor Sit Amet, Consectetuer Adipiscing Elit, Sed Diam Nonummy Nibh Euismod Tincidunt Ut Laoreet Dolore Magna Aliquam Erat Volutpat. Ut Wisi Enim Ad Minim Veniam, Quis Nostrud Exerci Tation Ullamcorper Suscipit Lobortis Nisl Ut Aliquip Ex Ea Commodo Consequat. Duis Autem Vel Eum Iriure Dolor In Hendrerit In Vulputate Velit Esse Molestie Consequat, Vel Illum Dolore Eu Feugiat Nulla Facilisis At Vero Eros Et Accumsan Et Iusto Odio Dignissim Qui Blandit Praesent Luptatum Zzril Delenit Augue Duis Dolore Te Feugait Nulla Facilisi. Lorem Ipsum Dolor Sit Amet, Consectetuer Adipiscing Elit.</p>
  <div class="abs about-rule"></div>
  <div class="abs btn" style="top:1068px;left:651px;width:127px;height:30px"><span class="btn-dot"></span>CONTACT US</div>
</section>

<section>
  <div class="abs services"></div>
  <p class="abs center kicker" style="top:1240px">Services</p>
  <h2 class="abs center heading" style="top:1256px;font-size:33px">What We Do</h2>
  <div class="abs underline" style="top:1300px"></div>
  <p class="abs center lead" style="top:1317px">Lorem ipsum dolor sit amet, consectetuer adipiscing elit, sed diam nonummy nibh euismod tincidunt ut laoreet dolore magna</p>

  <div class="abs service" style="top:1359px;left:109px">
    <svg class="ring" viewBox="0 0 140 140"><circle cx="70" cy="70" r="60" fill="#fff"/><path d="M70 6a64 64 0 1 0 64 64" fill="none" stroke="#0a93ec" stroke-width="6"/><path d="M55 56l15-7 15 7v10c0 9-7 15-15 18-8-3-15-9-15-18z" fill="none" stroke="#333" stroke-width="2"/><path d="M45 70v14l12 8M95 70v14l-12 8" fill="none" stroke="#333" stroke-width="2"/></svg>
    <p class="service-label">Liabilities<br>Insurance</p>
  </div>
  <div class="abs service" style="top:1359px;left:304px">
    <svg class="ring" viewBox="0 0 140 140"><circle cx="70" cy="70" r="60" fill="#fff"/><path d="M70 6a64 64 0 1 0 64 64" fill="none" stroke="#0a93ec" stroke-width="6"/><path d="M46 80h48v-8l-8-10H58l-8 10h-4z" fill="none" stroke="#333" stroke-width="2"/><circle cx="58" cy="82" r="4" fill="#333"/><circle cx="84" cy="82" r="4" fill="#333"/><path d="M84 46l8-3 8 3v6c0 5-4 8-8 10-4-2-8-5-8-10z" fill="none" stroke="#333" stroke-width="2"/></svg>
    <p class="service-label">Automobile<br>Insurance</p>
  </div>
  <div class="abs service hot" style="top:1359px;left:499px">
    <svg class="ring" viewBox="0 0 140 140"><circle cx="70" cy="70" r="60" fill="#fff"/><path d="M70 6a64 64 0 1 0 64 64" fill="none" stroke="#f2582a" stroke-width="6"/><path d="M48 86h44M52 86V60h36v26M52 68h36M58 60V50h24v10M60 76h6M74 76h6" fill="none" stroke="#f2582a" stroke-width="2"/></svg>
    <p class="service-label">Construction And<br>Engineering</p>
  </div>
  <div class="abs service" style="top:1359px;left:690px">
    <svg class="ring" viewBox="0 0 140 140"><circle cx="70" cy="70" r="60" fill="#fff"/><path d="M70 6a64 64 0 1 0 64 64" fill="none" stroke="#0a93ec" stroke-width="6"/><path d="M50 50l20-8 20 8v14c0 13-9 21-20 25-11-4-20-12-20-25z" fill="none" stroke="#333" stroke-width="2.5"/><path d="M66 56h8v8h8v8h-8v8h-8v-8h-8v-8h8z" fill="none" stroke="#333" stroke-width="2"/></svg>
    <p class="service-label">Casualty Workmen 's<br>Compensation Health Insurance</p>
  </div>
  <div class="abs service" style="top:1359px;left:886px">
    <svg class="ring" viewBox="0 0 140 140"><circle cx="70" cy="70" r="60" fill="#fff"/><path d="M70 6a64 64 0 1 0 64 64" fill="none" stroke="#0a93ec" stroke-width="6"/><rect x="46" y="54" width="48" height="22" fill="none" stroke="#333" stroke-width="2"/><circle cx="70" cy="65" r="7" fill="none" stroke="#333" stroke-width="2"/><circle cx="56" cy="86" r="4" fill="#333"/><circle cx="84" cy="86" r="4" fill="#333"/></svg>
    <p class="service-label">Marime And Transit<br>Credit</p>
  </div>
</section>

<section>
  <div class="abs testimonial" role="img" aria-label="Muted photo of business people behind the testimonial"></div>
  <p class="abs center" style="top:1694px;font-size:12px;color:#fff">Testimonial</p>
  <h2 class="abs center heading" style="top:1708px;font-size:31px;color:#fff">What Our Clients Say</h2>
  <p class="abs center" style="top:1760px;font-size:11px;color:#fff">Lorem ipsum dolor sit amet, consectetuer adipiscing elit, sed diam nonummy nibh euismod tincidunt ut laoreet dolore magna</p>
  <div class="abs avatar" role="img" aria-label="Client portrait photo"></div>
  <p class="abs" style="top:1815px;left:655px;color:#fff;font-size:12px">Clients Name</p>
  <p class="abs" style="top:1835px;left:655px;color:#fff;font-size:9.5px;font-style:italic">- Designer</p>
  <p class="abs quote" style="color:#fff">Lorem ipsum dolor sit amet, consectetuer adipiscing elit, sed diam nonummy nibh euismod tincidunt ut laoreet dolore magna aliquam erat volutpat. Ut wisi enim ad minim veniam, quis nostrud exerci tation ullamcorper suscipit lobortis nisl ut aliquip ex ea commodo consequat. Duis autem vel eum iriure dolor in hendrerit in vulputate velit esse molestie consequat, vel illum dolore eu feugiat nulla facilisis at vero eros et accumsan et iusto odio dignissim qui blandit praesent luptatum zzril delenit augue duis dolore te feugait nulla facilisi.</p>
  <div class="abs dots"><span></span><span class="on"></span><span></span></div>
</section>

<section>
  <p class="abs center kicker" style="top:2133px">Our Team</p>
  <h2 class="abs center heading" style="top:2146px;font-size:36px">Lantern insurance Team</h2>
  <div class="abs underline" style="top:2193px"></div>
  <p class="abs center lead" style="top:2200px">Lorem ipsum dolor sit amet, consectetuer adipiscing elit, sed diam nonummy nibh euismod tincidunt ut laoreet dolore magna</p>

  <article class="abs card" style="left:143px"><div class="card-photo" role="img" aria-label="Team member portrait photo"></div><p class="card-name">Your Name</p><p class="card-role">General Manager</p><p class="card-text">Lorem ipsum dolor sit amet, rtetuer adipiscinger elit werr werr veniam werwerr erewrer.</p></article>
  <article class="abs card" style="left:377px"><div class="card-photo" role="img" aria-label="Team member portrait photo"></div><p class="card-name">Your Name</p><p class="card-role">General Manager</p><p class="card-text">Lorem ipsum dolor sit amet, rtetuer adipiscinger elit werr werr veniam werwerr erewrer.</p></article>
  <div class="abs card-social"><span></span><span></span><span></span></div>
  <article class="abs card" style="left:611px"><div class="card-photo" role="img" aria-label="Team member portrait photo"></div><p class="card-name">Your Name</p><p class="card-role">General Manager</p><p class="card-text">Lorem ipsum dolor sit amet, rtetuer adipiscinger elit werr werr veniam werwerr erewrer.</p></article>
  <article class="abs card" style="left:846px"><div class="card-photo" role="img" aria-label="Team member portrait photo"></div><p class="card-name">Your Name</p><p class="card-role">General Manager</p><p class="card-text">Lorem ipsum dolor sit amet, rtetuer adipiscinger elit werr werr veniam werwerr erewrer.</p></article>
</section>

<section>
  <div class="abs contact"></div>
  <p class="abs kicker" style="top:2664px;left:145px">Get in Touch</p>
  <h2 class="abs heading" style="top:2684px;left:144px;font-size:36px">Contact Us</h2>
  <div class="abs field" style="top:2739px;left:143px;width:212px">First Name*</div>
  <div class="abs field" style="top:2739px;left:361px;width:213px">Last Name*</div>
  <div class="abs field" style="top:2791px;left:143px;width:212px">Email*</div>
  <div class="abs field" style="top:2791px;left:361px;width:213px">Company Name*</div>
  <div class="abs field" style="top:2844px;left:143px;width:212px">Your Tittle*</div>
  <div class="abs field" style="top:2844px;left:361px;width:213px">Phone*</div>
  <div class="abs field" style="top:2897px;left:143px;width:431px;height:96px">Message*</div>
  <div class="abs btn" style="top:3021px;left:140px;width:130px;height:31px"><span class="btn-dot"></span>SUBMIT</div>
  <div class="abs contact-photo" role="img" aria-label="Photo of a smiling businessman pointing at the form"></div>
</section>

<section>
  <div class="abs newsletter"></div>
  <svg class="abs" style="top:3143px;left:151px" width="36" height="36" viewBox="0 0 36 36"><circle cx="18" cy="18" r="16" fill="none" stroke="#fff" stroke-width="2"/><rect x="10" y="12" width="16" height="12" fill="#fff"/><path d="M10 12l8 7 8-7" fill="none" stroke="#0a93ec" stroke-width="1.5"/></svg>
  <p class="abs heading news-title">Newsletter Signup</p>
  <svg class="abs" style="top:3141px;left:438px" width="20" height="38" viewBox="0 0 20 38"><path d="M2 2l16 17L2 36" fill="none" stroke="#fff" stroke-width="2"/></svg>
  <div class="abs news-input">Your e-mail</div>
  <div class="abs btn" style="top:3143px;left:862px;width:120px;height:32px">SIGN UP</div>
</section>

<footer>
  <div class="abs footer"></div>
  <div class="abs map" role="img" aria-label="Street map showing the office location in Luanda with a red pin"></div>
  <svg class="abs" style="top:3195px;left:650px" width="28" height="319" viewBox="0 0 28 319"><path d="M0 0h0l26 160L0 319z" fill="#070707"/></svg>
  <svg class="abs" style="top:3308px;left:993px" width="20" height="28" viewBox="0 0 20 28"><path d="M10 27C4 18 2 14 2 10a8 8 0 0 1 16 0c0 4-2 8-8 17z" fill="#e3262b"/><circle cx="10" cy="10" r="3" fill="#fff"/></svg>

  <h3 class="abs heading foot-title" style="top:3237px;left:143px">QUICK LINK</h3>
  <div class="abs" style="top:3269px;left:143px;width:108px;height:1px;background:#333"></div>
  <div class="abs" style="top:3230px;left:342px;width:1px;height:200px;background:#222"></div>
  <ul class="abs foot-list" style="top:3278px;left:143px">
    <li class="active">HOME</li><li>WHO WE ARE</li><li>WHAT WE DO</li><li>OUR TEAM</li><li>CONTACT US</li>
  </ul>

  <h3 class="abs heading foot-title" style="top:3237px;left:414px">GET IN TOUCH</h3>
  <div class="abs f-row" style="top:3282px">
    <span class="f-icon"><svg width="12" height="14" viewBox="0 0 12 14"><path d="M6 13C2 8 1 6 1 5a5 5 0 0 1 10 0c0 1-1 3-5 8z" fill="#fff"/></svg></span>
    <div><p style="font-size:14px;font-weight:500">Lantern Insurance</p><p style="font-size:10px">Lorem Ipsum Dolor Sit Amet,<br>Adipiscinger Elit Werr.</p></div>
  </div>
  <div class="abs f-row" style="top:3352px;align-items:center">
    <span class="f-icon"><svg width="12" height="12" viewBox="0 0 12 12"><path d="M2 1l3 3-1 1.5a6 6 0 0 0 2.5 2.5L8 7l3 3-1.5 1.5C5 11.5.5 7 .5 2.5z" fill="#fff"/></svg></span>+555 014 2290
  </div>
  <div class="abs f-row" style="top:3410px;align-items:center">
    <span class="f-icon"><svg width="12" height="10" viewBox="0 0 12 10"><rect x="0" y="0" width="12" height="10" fill="#fff"/><path d="M0 0l6 5 6-5" fill="none" stroke="#0a93ec"/></svg></span>info@lanterninsure.example
  </div>
  <div class="abs" style="top:3462px;left:414px;display:flex;gap:8px">
    <span style="width:20px;height:20px;border-radius:50%;background:#fff"></span>
    <span style="width:20px;height:20px;border-radius:50%;background:#fff"></span>
    <span style="width:20px;height:20px;border-radius:50%;background:#fff"></span>
  </div>
  <p class="abs center copyright">Copyright 2019 Lantern Insurance Brokers. All Rights Reserved.</p>
</footer>

</body>
</html>
```